business card deign

Logo needs the following on it.
1. attached logo
2. Tagline - "If it keeps a drink cold or the party going...we do it!"
3. Name- Dalton Pikes, Founder and CPO
4. Address - 412 E. Carver Avenue, Ste 2207, Tampa, FL. 33917
5. Phone - 555.318.4726

```html
<!DOCTYPE html>
<html lang="en">
<head>
<meta charset="UTF-8">
<title>Hopwell Business Card</title>
<link href="https://fonts.googleapis.com/css2?family=Open+Sans:wght@400;600;700;800&display=swap" rel="stylesheet">
<style>
  :root {
    --backdrop: #222222;
    --gold-deep: #8c6234;
    --gold-mid: #c59a5e;
    --gold-light: #f8e8a8;
    --gold-warm: #d4aa66;
    --gold-edge: #a9763a;
    --ink-white: #ffffff;
    --ink-bronze: #7a5428;
  }
  * { margin: 0; padding: 0; box-sizing: border-box; }
  html, body {
    width: 1200px;
    height: 711px;
    overflow: hidden;
    background: var(--backdrop);
    font-family: "Open Sans", Arial, sans-serif;
  }
  .stage {
    position: relative;
    width: 1200px;
    height: 711px;
  }
  .card {
    position: absolute;
    top: 205px;
    width: 520px;
    height: 300px;
    border-radius: 22px;
    overflow: hidden;
    background: linear-gradient(112deg,
      var(--gold-deep) 0%,
      var(--gold-mid) 28%,
      var(--gold-light) 50%,
      var(--gold-warm) 70%,
      var(--gold-edge) 100%);
  }
  .card--front { left: 60px; }
  .card--back { left: 620px; }

  .brand-front {
    position: absolute;
    left: 0;
    right: 0;
    top: 118px;
    text-align: center;
    font-weight: 800;
    font-size: 54px;
    letter-spacing: 18px;
    text-indent: 18px;
    color: var(--ink-bronze);
    text-transform: uppercase;
  }

  .brand-back {
    position: absolute;
    right: 34px;
    top: 46px;
    font-weight: 800;
    font-size: 26px;
    letter-spacing: 9px;
    color: var(--ink-white);
    text-transform: uppercase;
  }

  .contact {
    position: absolute;
    left: 44px;
    bottom: 30px;
    color: var(--ink-white);
  }
  .contact__head {
    position: relative;
    padding-left: 22px;
    margin-bottom: 12px;
  }
  .contact__bar {
    position: absolute;
    left: 0;
    top: 4px;
    width: 10px;
    height: 50px;
    background: var(--ink-white);
  }
  .contact__name {
    font-weight: 700;
    font-size: 26px;
    line-height: 1.1;
  }
  .contact__role {
    font-weight: 600;
    font-size: 15px;
    line-height: 1.4;
  }
  .contact__tagline {
    padding-left: 40px;
    font-size: 13px;
    line-height: 1.35;
    margin-bottom: 10px;
  }
  .contact__line {
    display: flex;
    align-items: flex-start;
    gap: 8px;
    padding-left: 70px;
    font-size: 13px;
    line-height: 1.35;
  }
  .contact__icon {
    width: 13px;
    height: 13px;
    flex: none;
    margin-top: 3px;
  }
</style>
</head>
<body>
  <main class="stage">
    <section class="card card--front" aria-label="Card front">
      <div class="brand-front">Hopwell</div>
    </section>

    <section class="card card--back" aria-label="Card back">
      <div class="brand-back">Hopwell</div>

      <div class="contact">
        <div class="contact__head">
          <span class="contact__bar"></span>
          <div class="contact__name">Dalton Pikes</div>
          <div class="contact__role">Founder and CPO</div>
        </div>
        <p class="contact__tagline">If it keeps a drink cold or<br>the party going...we do it!</p>
        <div class="contact__line">
          <svg class="contact__icon" viewBox="0 0 24 24" aria-hidden="true">
            <path fill="#fff" d="M6.6 10.8a15.1 15.1 0 0 0 6.6 6.6l2.2-2.2a1 1 0 0 1 1-.25 11.4 11.4 0 0 0 3.6.57 1 1 0 0 1 1 1V20a1 1 0 0 1-1 1A17 17 0 0 1 3 4a1 1 0 0 1 1-1h3.5a1 1 0 0 1 1 1c0 1.25.2 2.45.57 3.57a1 1 0 0 1-.25 1z"/>
          </svg>
          <span>555.318.4726</span>
        </div>
        <div class="contact__line">
          <svg class="contact__icon" viewBox="0 0 24 24" aria-hidden="true">
            <path fill="none" stroke="#fff" stroke-width="2.4" d="M12 22s-7-7.2-7-12a7 7 0 0 1 14 0c0 4.8-7 12-7 12z"/>
            <circle cx="12" cy="10" r="2.6" fill="#fff"/>
          </svg>
          <span>412 E. Carver Avenue,<br>Ste 2207, Tampa, FL. 33917</span>
        </div>
      </div>
    </section>
  </main>
</body>
</html>
```